Business Card Design

I need a business card design for my new business based on Long Island, NY also serving NYC called Pawhaven Retreat. I have built a website with cardmint that can be looked at as a basis for the card. It is pawhavenretreat.com.

I board Labrador Retrievers in my home. Specialize in one breed. Cage free environment. Dogs have full run of home and fenced in property. Pawhaven Retreat is a one-of-a-kind, high-quality dog-boarding provider serving specifically Labrador Retrievers. By working with a dog I am comfortable with, I am able to offer the best care for all pets that come through my door. I work with Lab owners in the Long Island/NYC area to provide an
in-home safe, reliable and fun environment for daycare and overnight stays.

I provide a unique boarding experience for Labrador Retrievers on Long Island. Your Lab should be well mannered, housebroken and good with other dogs. Provided your pet is well mannered and house trained, my boarding services allow dogs to experience a cage-free stay while having free roam of my home and property. This allows owners a unique alternative to a kennel, giving pets the chance to experience a home away from home rather than chain linked fences and cold concrete floors.
As a guest at Pawhaven Retreat, your dog will get:

4-star kibble
Access to my in-ground pool
All-natural snack selection
Companionship of other retrievers including my two
Full run of entire home and fenced-in backyard
Photos AND videos posted to Snapgram so you can see your dog having fun while away
Toys, bones and affection

I think it is important to have a pic of the 3 colored labs below. Also the picture of my own personal labs ..the white one with the black puppy. Maybe some paw prints. If using any imagery that MUST look EXACTLY like labrador retriever no generic dogs. Thank you
Updates

The Back of the Card should have the following: The background should be one of the pictures I sent (white dog in pool or another pic I included) At Pawhaven Retreat your Lab gets: Cage Free Environment Full run of my home and fenced in yard In-ground pool Toys and affection Companionship of other Labrador Retrievers Photos and Videos posted Snapgram of your loved one FRONT OF THE CARD: should include picture of the 3 labs (yellow white brown) OR picture of white dog in pool. Pawhaven Retreat should be in larger font than the rest. the following can be in any order. Tom Pelley Commack, NY in Central Long Island pawhavenretreat.com 631-555-0192

Industry/Entity Type

Environment

Contact Information for Business Card

Pawhaven Retreat
Commack, NY
Tom Pelley
hello@pawhavenretreat.com
631-555-0192

```html
<!DOCTYPE html>
<html lang="en">
<head>
<meta charset="utf-8">
<title>Pawhaven Retreat – Business Card</title>
<link href="https://fonts.googleapis.com/css2?family=Gelasio:wght@700&family=Arimo:wght@400&display=swap" rel="stylesheet">
<style>
  :root{
    --bg:#e9e4df;
    --card:#ffffff;
    --ink:#111111;
    --accent:#9a5a2e;
    --grass:#7d9a4e;
    --grass-dark:#55702f;
    --coat-dark:#2a1d17;
    --coat-light:#e9dcc0;
    --sky:#a9bb7c;
  }
  *{margin:0;padding:0;box-sizing:border-box}
  html,body{width:1200px;height:914px;overflow:hidden;background:var(--bg)}
  .canvas{position:relative;width:1200px;height:914px}
  .card{position:absolute;left:250px;width:700px;height:400px;background:var(--card);
        box-shadow:0 3px 10px rgba(0,0,0,.18);overflow:hidden}
  .card--front{top:40px}
  .card--back{top:474px}

  /* front */
  .front-photo{position:absolute;inset:0;
    background:linear-gradient(180deg,var(--sky) 0%,var(--coat-dark) 30%,var(--coat-light) 45%,var(--coat-dark) 62%,var(--grass) 82%,var(--grass-dark) 100%)}
  .front-curve{position:absolute;inset:0}
  .front-info{position:absolute;right:40px;top:72px;text-align:right;color:var(--ink)}
  .brand,.brand-town{font-family:"Gelasio",Georgia,serif;font-weight:700;font-size:30px;line-height:1.05}
  .owner{font-family:"Arimo",Arial,sans-serif;font-size:24px;margin-top:30px}
  .contact{list-style:none;margin-top:34px;font-family:"Arimo",Arial,sans-serif;font-size:18px}
  .contact li{display:flex;align-items:center;justify-content:flex-end;gap:12px;margin-top:6px}
  .contact svg{width:18px;height:14px;fill:var(--accent)}

  /* back */
  .back-heading{position:absolute;left:46px;top:36px;font-family:"Gelasio",Georgia,serif;font-weight:700;font-size:24px;color:var(--ink)}
  .perks{position:absolute;left:46px;top:86px;list-style:none;font-family:"Arimo",Arial,sans-serif;font-size:17px;line-height:1.2;color:var(--ink)}
  .perks li{position:relative;padding-left:26px}
  .perks li::before{content:"";position:absolute;left:0;top:4px;width:12px;height:12px;border-radius:50%;background:var(--accent)}
  .back-photo{position:absolute;right:0;bottom:0;width:300px;height:170px;
    background:linear-gradient(180deg,#ffffff 0%,var(--coat-dark) 25%,var(--coat-light) 50%,var(--coat-dark) 70%,var(--grass) 88%,var(--grass-dark) 100%);
    border-top-left-radius:60px 40px}
</style>
</head>
<body>
<main class="canvas">
  <section class="card card--front">
    <div class="front-photo" role="img" aria-label="Photo of three Labrador Retrievers – chocolate, yellow and black – sitting on grass"></div>
    <svg class="front-curve" viewBox="0 0 700 400" aria-hidden="true">
      <ellipse cx="800" cy="230" rx="460" ry="600" fill="var(--accent)"/>
      <ellipse cx="800" cy="230" rx="450" ry="594" fill="var(--card)"/>
    </svg>
    <div class="front-info">
      <h1 class="brand">Pawhaven Retreat</h1>
      <p class="brand-town">Commack</p>
      <p class="owner">NY Tom Pelley</p>
      <ul class="contact">
        <li>631-555-0192
          <svg viewBox="0 0 18 14" aria-hidden="true"><path d="M1 5c0-3 16-3 16 0v2h-4V5H5v2H1zM4 8h10l2 6H2z"/></svg>
        </li>
        <li>hello@pawhavenretreat.com
          <svg viewBox="0 0 18 14" aria-hidden="true"><path d="M0 0h18v14H0zM1.5 1.5 9 8l7.5-6.5z" fill-rule="evenodd"/></svg>
        </li>
      </ul>
    </div>
  </section>

  <section class="card card--back">
    <h2 class="back-heading">As a guest at Pawhaven Retreat, your dog will get:</h2>
    <ul class="perks">
      <li>4-star kibble</li>
      <li>Access to my in-ground pool</li>
      <li>All-natural snack selection</li>
      <li>Companionship of other retrievers including my two</li>
      <li>Full run of entire home and fenced-in backyard</li>
      <li>Photos AND videos posted to Snapgram<br>so you can see your dog having fun while away</li>
      <li>Toys, bones and affection</li>
    </ul>
    <div class="back-photo" role="img" aria-label="Photo of three Labrador Retrievers sitting together on grass"></div>
  </section>
</main>
</body>
</html>
```